Flyer Design Project for high quality paving products for landscaping

Corvell paving stones is a long established manufacturer and supplier of concrete paving, pool coping and landscape features.
it is known as a premium, top end product which over recent years has lost market share to imported natural stone which is in some cases a lot cheaper. There is a perception that natural stone is better and now also cheaper.

I think a lot of the information required for the flyer is already on our web site www.corvell-example.com.au We service the following types of customers; Architects, Pool Builders, Landscape designers, Landscape contractors and private customers. A lot of times our product is specified by a designer and then the private customer comes to our showroom for final selection. The main purpose of this flyer would to give to the private customer when they come to us for final selection, reinforcing the value of our brand and product.

Target Market(s)

Middle to upper class who have paid for a designer. Like our product but cant help being drawn to a cheaper alternative.

Industry/Entity Type

Landscaping

Requirements
Must have
• Must use existing Corvell logo.
Nice to have
• We have one awards. Gold medals. Landscaping is very visual. Images as well as inspirational text. Not to technical.

I think of Corvell as Valtrane. THey have Sports cars, Luxury cars, Commercial vehicles, family cars. Wide customer base but always with valtrane branding and quality.
Should not have
• Want to let people know we can supply products that are affordable if they have a budget without compromising our brand as atop end product.

```html
<!DOCTYPE html>
<html lang="en">
<head>
<meta charset="utf-8">
<title>Corvell Paving Stones – Trifold Flyer</title>
<link href="https://fonts.googleapis.com/css2?family=Lato:wght@300;400;700&display=swap" rel="stylesheet">
<style>
  :root {
    --bg: #eeeeef;
    --panel: #2a2a2b;
    --panel-light: #3a3a3c;
    --band: #555557;
    --text: #d4d4d6;
    --text-soft: #a9a9ad;
    --white: #ffffff;
    --photo-sky: #6f8fb0;
    --photo-warm: #b67a45;
    --photo-pool: #4a7fa6;
    --photo-green: #4f7d3a;
    --photo-stone: #c9cdd2;
  }
  * { box-sizing: border-box; margin: 0; padding: 0; }
  html, body {
    width: 1200px; height: 905px; overflow: hidden;
    background: var(--bg);
    font-family: "Lato", Arial, sans-serif;
  }
  .flyer {
    position: absolute; left: 60px; top: 142px;
    width: 1080px; height: 620px;
    display: flex;
    box-shadow: 0 12px 30px rgba(0,0,0,.18);
  }
  .panel {
    width: 360px; height: 620px;
    background: linear-gradient(160deg, var(--panel-light) 0%, var(--panel) 45%, var(--panel) 100%);
    color: var(--text);
    display: flex; flex-direction: column;
    border-right: 1px solid #1c1c1d;
    overflow: hidden;
  }
  .panel:last-child { border-right: none; }
  .brand-block { padding: 26px 28px 10px; }
  .brand-name {
    font-weight: 400; font-size: 18px; line-height: 1.2;
    color: var(--white);
  }
  .heading {
    font-weight: 300; font-size: 17px; line-height: 1.3;
    color: var(--text); padding: 6px 28px 12px;
  }
  .copy {
    font-weight: 300; font-size: 10.5px; line-height: 1.55;
    color: var(--text-soft); padding: 0 28px 10px;
  }
  .band {
    background: var(--band);
    color: var(--white);
    font-weight: 300; font-size: 15px;
    padding: 8px 28px; margin: 8px 0 12px;
  }
  .middle-top { padding-bottom: 12px; }
  .reason-title { font-weight: 700; font-size: 14px; color: var(--white); padding: 4px 28px 0; }
  .reason-sub { font-size: 9px; letter-spacing: 1px; text-transform: uppercase; color: var(--text-soft); padding: 3px 28px 0; }
  .reason-line { font-weight: 300; font-size: 11px; color: var(--text); padding: 2px 28px 0; }
  .photo { width: 100%; display: block; }
  .photo-building { height: 150px; background: linear-gradient(180deg, var(--photo-sky) 0%, #a9b7c4 45%, var(--photo-warm) 70%, #5b4a3a 100%); }
  .photo-pool { height: 120px; background: linear-gradient(180deg, #2f3b46 0%, var(--photo-pool) 55%, #9ec3d8 100%); }
  .photo-garden { flex: 1; background: linear-gradient(180deg, #7ea36a 0%, var(--photo-green) 60%, #e4e6e2 100%); }
  .photo-steps { flex: 1; margin-top: 6px; background: linear-gradient(150deg, #e9ecef 0%, var(--photo-stone) 40%, #6f9a55 75%, #3f6a2e 100%); }
  .right-top { padding-top: 26px; }
</style>
</head>
<body>
  <main class="flyer">
    <section class="panel panel-left">
      <div class="brand-block">
        <div class="brand-name">Corvell paving stones</div>
      </div>
      <h1 class="heading">Corvell Paving Stones: Granite Pavers &amp; Pool Coping Melbourne</h1>
      <p class="copy">For more than four decades Corvell has crafted premium concrete pavers, pool coping and landscape features for homes across Australia. Every stone is made locally with care, tested for strength and finished by hand so your outdoor space looks refined for years to come.</p>
      <p class="copy">Our range is specified by leading architects and designers, and our showroom team will help you make the final selection with confidence.</p>
      <h2 class="band">what we do</h2>
      <p class="copy">We start by sourcing the finest natural stone aggregates and blending them into pavers built for the Australian climate, from pool surrounds to garden paths.</p>
      <p class="copy">Corvell Paving Stones are available in a wide range of styles, colours and sizes, and bespoke pieces are crafted by our own team.</p>
    </section>

    <section class="panel panel-middle">
      <div class="middle-top">
        <div class="brand-block">
          <div class="brand-name">Corvell paving stones</div>
        </div>
        <p class="copy">Made in our own workshop, working closely with architects and designers. We are proud to be the first carbon neutral paver maker in Australia.</p>
        <h2 class="reason-title">Five reasons to choose Corvell</h2>
        <div class="reason-sub">durability</div>
        <p class="reason-line">Both beautiful and strong – your landscape deserves Corvell.</p>
      </div>
      <div class="photo photo-building" role="img" aria-label="Photo of a modern home with warm lit timber facade at dusk"></div>
      <div class="photo photo-pool" role="img" aria-label="Photo of a long pool lined with pale stone coping"></div>
      <div class="photo photo-garden" role="img" aria-label="Photo of a formal garden with clipped hedges and paved paths"></div>
    </section>

    <section class="panel panel-right">
      <div class="right-top">
        <p class="copy">Our pavers resist stains, fading and frost, so they keep their colour and finish season after season. Each piece is sealed for easy care.</p>
        <p class="copy">Because they are made to exacting standards, you can lay them with confidence knowing every stone fits.</p>
      </div>
      <h2 class="band">community</h2>
      <p class="copy">Corvell supports local landscape schools and partners with growers to plant a tree for every project we supply.</p>
      <h2 class="band">landscape features</h2>
      <p class="copy">Within our range are steps, seats and planters made to match so your whole garden feels complete.</p>
      <div class="photo photo-steps" role="img" aria-label="Photo of pale stone garden steps with grass strips and a stone sphere"></div>
    </section>
  </main>
</body>
</html>
```